8'x8' Exhibit Backdrop for Healthcare Events focused on the 55 and older crowds

8X8 Backdrop for Exhibiting.

I also want a design for a 6' table skirt to include our logo on two sides and the logo with Hereditary Cancer Screening underneath on the front. I want the main message of Will You Give your Loved Ones The Information To Beat Cancer in Their Lives to be completely centered on the 8X8 backdrop. Hereditary Cancer Screening The Test You Take For Them in the top left corner and the purple box on the right hand side - just like the photo that has been uploaded below. I need High resolution photos around the backdrop but not so large that they overtake the main message.

Target Market(s)

55+ crowd living in Adult only communities. They have an active lifestyle

Industry/Entity Type

Healthcare

Other font styles liked:
• "The Test You Take For Them" is Comic Sans

Colors
0255a3
fbed22
ffffff

Requirements
Must have
• I am posting a photo of the exact backdrop I would like to see. There are red arrows showing where to move certain items. There is a space underneath the slogan WILL YOU GIVE YOUR LOVED ONES... where another photo will go. Add another photo underneath the slogan that you are moving up - GIVE THEM THE GIFT OF KNOWLEDGE
• See the upload section for the new photo
• Do this one exactly like I am asking for and then you can show me some of your ideas. Thanks
• THE PHOTOS UPLOADED ARE EXAMPLES. FEEL FREE TO SEARCH OUT YOUR OWN HIGH RESOLUTION PHOTOS. THANKS

```html
<!DOCTYPE html>
<html lang="en">
<head>
<meta charset="utf-8">
<title>Hereditary Cancer Screening – Exhibit Backdrop</title>
<link href="https://fonts.googleapis.com/css2?family=Arimo:wght@400;700&family=Roboto+Condensed:wght@400;700&family=Archivo:wght@800&family=Comic+Neue:wght@400;700&display=swap" rel="stylesheet">
<style>
  :root{
    --navy:#1b2383;
    --panel:#211f78;
    --ink:#111111;
    --green:#62e02b;
    --white:#ffffff;
    --page:#e9e9ec;
  }
  html,body{margin:0;padding:0;width:1200px;height:1200px;overflow:hidden;background:var(--page);}
  .backdrop{position:relative;width:1200px;height:1200px;background:var(--white);overflow:hidden;font-family:"Arimo",sans-serif;}
  .photo{position:absolute;}

  /* title block */
  .title{position:absolute;left:20px;top:70px;width:330px;text-align:right;color:var(--navy);line-height:1;}
  .title .t1{font-weight:700;font-size:66px;letter-spacing:-0.5px;}
  .title .t2,.title .t3{font-weight:400;font-size:66px;margin-top:4px;}
  .tagline{position:absolute;left:38px;top:300px;width:312px;height:26px;background:var(--green);color:var(--white);
    font-family:"Comic Neue",cursive;font-size:20px;line-height:26px;text-align:center;}

  /* central message */
  .message{position:absolute;left:240px;top:350px;width:520px;height:440px;font-family:"Roboto Condensed",sans-serif;color:var(--ink);}
  .line{position:absolute;left:22px;white-space:nowrap;line-height:1;}
  .l1{top:28px;font-size:66px;}
  .l1 b{font-family:"Archivo",sans-serif;font-weight:800;font-size:60px;}
  .l2{top:104px;font-size:62px;}
  .band{position:absolute;left:0;top:176px;width:520px;height:80px;background:var(--ink);}
  .band-lower{position:absolute;left:0;top:256px;width:250px;height:78px;background:var(--ink);}
  .l3{top:186px;font-size:60px;font-weight:700;color:var(--white);}
  .l4{top:264px;font-size:60px;font-weight:700;color:var(--white);}
  .cancer{position:absolute;left:264px;top:280px;font-family:"Archivo",sans-serif;font-weight:800;font-size:50px;color:var(--green);line-height:1;}
  .l5{top:356px;font-size:64px;}
  .rule-h{position:absolute;left:240px;top:810px;width:520px;height:14px;background:var(--ink);}
  .rule-v{position:absolute;left:272px;top:824px;width:12px;height:376px;background:var(--ink);}

  /* right panel */
  .panel{position:absolute;left:765px;top:0;width:435px;height:855px;background:var(--panel);color:var(--white);}
  .panel-photo{left:0;top:0;width:435px;height:420px;background:linear-gradient(180deg,#6c6fd0 0%,#4e4fb4 60%,var(--panel) 100%);}
  .gift{position:absolute;right:50px;top:480px;text-align:right;line-height:1;}
  .gift .g1{font-family:"Archivo",sans-serif;font-weight:800;font-size:44px;}
  .gift .g1 span{font-family:"Roboto Condensed",sans-serif;font-weight:400;}
  .gift .g2{font-family:"Roboto Condensed",sans-serif;font-size:32px;}
  .gift .g3{font-family:"Archivo",sans-serif;font-weight:800;font-size:40px;letter-spacing:1px;}
  .knowing{position:absolute;right:50px;top:612px;width:360px;text-align:right;font-family:"Comic Neue",cursive;font-weight:700;font-size:27px;line-height:1.35;}
  .bulb{position:absolute;right:58px;top:700px;width:100px;height:100px;}
  .power{position:absolute;right:50px;top:820px;font-family:"Arimo",sans-serif;font-weight:700;font-size:21px;color:var(--green);}
  .power::before{content:"";display:inline-block;width:15px;height:15px;background:var(--green);margin-right:4px;vertical-align:-1px;}

  /* brand */
  .brand{position:absolute;left:40px;top:985px;display:flex;align-items:center;gap:12px;}
  .brand-dot{width:60px;height:60px;border-radius:50%;background:var(--navy);}
  .brand-name{font-family:"Arimo",sans-serif;font-weight:700;font-size:26px;line-height:1.05;color:var(--navy);}
</style>
</head>
<body>
<main class="backdrop">

  <div class="title">
    <div class="t1">Hereditary</div>
    <div class="t2">Cancer</div>
    <div class="t3">Screening</div>
  </div>
  <div class="tagline">"The Test You Take For Them"</div>

  <div class="photo" role="img" aria-label="Photo of a smiling multigenerational family seated outdoors" style="left:380px;top:20px;width:370px;height:320px;background:linear-gradient(160deg,#9fbf6e 0%,#d9c3a8 45%,#e8d2c0 75%,#8aa0c2 100%);"></div>

  <div class="photo" role="img" aria-label="Photo of a smiling grandfather with his granddaughter" style="left:0;top:350px;width:236px;height:240px;background:linear-gradient(135deg,#e8e4dc 0%,#a06a4a 45%,#e58aa0 100%);"></div>
  <div class="photo" role="img" aria-label="Photo of grandparents laughing with two grandchildren" style="left:0;top:598px;width:236px;height:300px;background:linear-gradient(150deg,#d8cfc4 0%,#e4c2a6 45%,#3f6fbf 100%);"></div>

  <section class="message">
    <div class="band"></div>
    <div class="band-lower"></div>
    <div class="line l1">WILL YOU <b>GIVE</b></div>
    <div class="line l2">YOUR LOVED ONES</div>
    <div class="line l3">THE INFORMATION</div>
    <div class="line l4">TO BEAT</div>
    <div class="cancer">CANCER</div>
    <div class="line l5">IN THEIR LIVES ?</div>
  </section>
  <div class="rule-h"></div>
  <div class="rule-v"></div>

  <div class="photo" role="img" aria-label="Photo of grandparents and parents gathered around a baby and a young child" style="left:305px;top:840px;width:455px;height:360px;background:linear-gradient(135deg,#f2e6dc 0%,#d6a68a 40%,#f0d6cc 70%,#c9b8ae 100%);"></div>

  <aside class="panel">
    <div class="photo panel-photo" role="img" aria-label="Blue-toned photo of a grandmother and grandchildren sitting on a garden bridge"></div>
    <div class="gift">
      <div class="g1">GIVE <span>THEM</span></div>
      <div class="g2">THE GIFT OF</div>
      <div class="g3">KNOWLEDGE</div>
    </div>
    <div class="knowing">Knowing is better than<br>not knowing.</div>
    <svg class="bulb" viewBox="0 0 100 100" aria-hidden="true">
      <g fill="none" stroke="var(--green)" stroke-width="7" stroke-linecap="round">
        <path d="M38 70 C28 60 26 50 32 42 C38 34 54 32 62 40 C70 48 68 60 60 68 L58 80 L42 80 Z" stroke-linejoin="round"/>
        <line x1="44" y1="90" x2="58" y2="90"/>
        <line x1="50" y1="8" x2="50" y2="20"/>
        <line x1="22" y1="18" x2="30" y2="27"/>
        <line x1="78" y1="18" x2="70" y2="27"/>
        <line x1="8" y1="42" x2="20" y2="44"/>
        <line x1="92" y1="42" x2="80" y2="44"/>
      </g>
    </svg>
    <div class="power">Knowledge is Power</div>
  </aside>

  <div class="photo" role="img" aria-label="Photo of a grandfather cheek to cheek with his granddaughter" style="left:770px;top:865px;width:210px;height:225px;background:linear-gradient(135deg,#f4f1ea 0%,#8a5a40 50%,#4a3426 100%);"></div>
  <div class="photo" role="img" aria-label="Black and white photo of a grandmother hugged by her granddaughter" style="left:990px;top:865px;width:210px;height:225px;background:linear-gradient(135deg,#d8d8d8 0%,#8a8a8a 50%,#3a3a3a 100%);"></div>
  <div class="photo" role="img" aria-label="Black and white photo of a grandmother and granddaughter laughing together" style="left:770px;top:1098px;width:210px;height:102px;background:linear-gradient(135deg,#eeeeee 0%,#a0a0a0 55%,#5a5a5a 100%);"></div>
  <div class="photo" role="img" aria-label="Photo of grandparents smiling with two grandchildren" style="left:990px;top:1098px;width:210px;height:102px;background:linear-gradient(135deg,#d8cfc4 0%,#e4c2a6 50%,#3f6fbf 100%);"></div>

  <div class="brand">
    <div class="brand-dot"></div>
    <div class="brand-name">KINWELL<br>HEALTH<br>GROUP</div>
  </div>

</main>
</body>
</html>
```